Finding the Root: Reason in Clinical Choice-Crafting

I'd like a cover that looks like it would fit on the shelf next to "The Illness Mirage" by Corwin Talley, "The Close of Forgetting" by Hugh Marchetti, "Meal Mend" by Paul Grieve, "The Energy Restart Plan" by Oscar Pemberley or "The Gland Restart Plan" by the same or "The Cortex Restart Plan" by the same ... either text only (with some interesting fonts that make the title stand out, and the subtitle smaller) or a relevant image, though I'm not entirely sure what that would be since this is a book about big-picture medical decision making.
Author name is Dr Tessa Morrow, NMD
I'll eventually request an e-book, paperback, and audio cover from the winner...

Target Market(s)

practicing physicians

Industry/Entity Type

medicine

Requirements
Must have
• look similar to other books in the genre

```html
<!DOCTYPE html>
<html lang="en">
<head>
<meta charset="utf-8">
<title>Finding the Root — Book Cover</title>
<link rel="stylesheet" href="https://fonts.googleapis.com/css2?family=Tinos:ital@0;1&family=EB+Garamond:wght@500;600&display=swap">
<style>
  :root {
    --backdrop: #020508;
    --paper: #f5f5f5;
    --leaf: #96ba40;
    --leaf-dark: #6f8f3a;
    --ink: #0a0a0a;
    --stone: #a5a5a5;
    --muted: #8c8c8c;
  }
  html, body {
    margin: 0;
    padding: 0;
    width: 1200px;
    height: 1200px;
    overflow: hidden;
    background: var(--backdrop);
  }
  .book-cover {
    position: absolute;
    left: 273px;
    top: 109px;
    width: 654px;
    height: 982px;
    background: var(--paper);
  }
  .book-cover svg { display: block; width: 654px; height: 982px; }
  .endorsement-frame { fill: none; stroke: var(--stone); stroke-width: 1.2; stroke-dasharray: 10 7; }
  .endorsement-text { font-family: "Tinos", serif; font-style: italic; font-size: 15px; fill: var(--muted); }
  .endorsement-rule { stroke: var(--leaf); stroke-width: 1; }
  .title-main { font-family: "Tinos", serif; fill: var(--ink); }
  .title-word { font-size: 162px; letter-spacing: -4px; }
  .title-small { font-size: 162px; letter-spacing: -4px; }
  .title-accent { font-family: "Tinos", serif; font-size: 174px; fill: var(--leaf); }
  .maze-area { fill: url(#mazeTone); }
  .subtitle-rule { stroke: var(--leaf-dark); stroke-width: 1; }
  .subtitle { font-family: "EB Garamond", serif; font-weight: 500; font-size: 35px; letter-spacing: 9px; fill: #231f20; }
  .author-band { fill: var(--leaf); }
  .author-name { font-family: "EB Garamond", serif; font-weight: 600; font-size: 56px; fill: var(--ink); }
</style>
</head>
<body>
  <div class="book-cover">
    <svg viewBox="0 0 654 982" xmlns="http://www.w3.org/2000/svg">
      <defs>
        <linearGradient id="mazeTone" x1="0" y1="0" x2="1" y2="0">
          <stop offset="0" stop-color="#e2e2e2"/>
          <stop offset="0.5" stop-color="#d8dccf"/>
          <stop offset="1" stop-color="#e2e2e2"/>
        </linearGradient>
      </defs>

      <g class="endorsement">
        <rect class="endorsement-frame" x="97" y="32" width="461" height="101"/>
        <text class="endorsement-text" x="327" y="80" text-anchor="middle">[ ENDORSEMENT GOES HERE]</text>
        <line class="endorsement-rule" x1="257" y1="113" x2="398" y2="113"/>
      </g>

      <g class="title-main">
        <text class="title-word" x="327" y="287" text-anchor="middle">Finding</text>
        <text class="title-small" x="327" y="400" text-anchor="middle">the</text>
      </g>
      <text class="title-accent" x="327" y="551" text-anchor="middle">ROOT</text>

      <rect class="maze-area" x="77" y="594" width="500" height="120" role="img" aria-label="Maze illustration with a green path winding from an entry ring to an arrow on the right"/>

      <line class="subtitle-rule" x1="94" y1="743" x2="555" y2="743"/>
      <text class="subtitle" x="329" y="793" text-anchor="middle">REASON IN CLINICAL</text>
      <text class="subtitle" x="329" y="835" text-anchor="middle">CHOICE-CRAFTING</text>
      <line class="subtitle-rule" x1="94" y1="855" x2="555" y2="855"/>

      <rect class="author-band" x="0" y="884" width="654" height="98"/>
      <text class="author-name" x="327" y="948" text-anchor="middle">Dr Tessa Morrow, NMD</text>
    </svg>
  </div>
</body>
</html>
```